Systems and Technology Consultants - Website

Design & Build a website for a new company which operates in the Systems and Technology space for Transportation, Government and Commercial sectors.

Overall design should be minimalist in nature.
Should also have a feed that provides news and event updates on the main page.
Logo has already been awarded and should be incorporated into the site.

We like the overall layout, functionality and simplicity of the below sites. Submitted designs could be similar to or a combination of the aspects on these sites, or perhaps a whole different concept - we are open to new ideas.
Norvique.com
Teblo.it

Update 1 Dated 27 May 2014

All I am moving away from the Teblo.it website and would like it to be more aligned with Norvique.com not only in layout but in functionality. I will be extending the deadline of this design brief for two weeks to incorporate additional requirements and will add addtional funding to the project.

Apologies for not having more information available to provide but with so many submissions its getting confusing.

Thanks Derek

Please note that the brief has been updated and the deadline has been extended.

Important: We will need two language versions of the website, English and Arabic; the website is hosted on HostPelican

Hello All, Thank you for your submissions. We have narrowed it down to the final 6 designers and I just wanted to take a moment and provide a bit of feedback regarding the concepts that we like and the modifications we are looking for. First, let me mention some of the design functions we like. - At the top of the homepage we really like the "region" or "language" tab so that the website can be viewed in both English and Arabic. - We like the homepage to have clear color variation so that the different sections of the homepage are distinct. Additionally, we like the bottom portion of the homepage to be in red. We feel that draws attention to our contact information. Again, we would like the colors to integrate black, gray-scale, red, etc. - Having a search tab at the top of the home page, or integrated into the main image, so that the site is easy to navigate. - We especially like the main image to have the scrolling tabs at the bottom so it is easy to browse the services offered (Consultancy, Solutions Architecture, Masters Systems Integration, Independent Design Review). - In regards to the services offered tab we really like the idea that a few people presented that have the outside of our logo with an icon in the middle of consultancy, solutions, etc., etc. Secondly, as mentioned in our brief we really enjoy the design of norvique site. Specially, we enjoy the strong iconic images they use, the way the tabs at the top scroll easily, and contact us page that generates an email. Lastly, I've included some photos of the concept we have been working on. What we are trying to demonstrate is how our company offers a range of services that are essentially linked together. We provide individual services that when combined present the full service package. We would like this concept to be integrated into the over concept of our website. Please feel free to ask for clarification of any of the above points or contact us if you have any additional questions. We appreciate all of your hard work and are very excited to see the updated designs. Best, Marta Vennick Quelbrant Senior Program Manager marta.vennick@quelbrant-example.com

Industry/Entity Type

Government

Font styles to use
Serif
Sans Serif

Requirements
Must have
• Must work on/adapt to various/mobile devices (responsive)
Must be simple and straightforward
Colors should be in line/matching with logo
2 language versions: English and Arabic (no Thai)
Services should be the first group/row of items after/below the main image
Note: the website will be hosted by hostpelican
Nice to have
• Submit feedback form
What's New section
The banner at the bottom of the site should not be too large; we would like a narrow one more
It would be nice if the header/top banner (with Home, About, etc. tabs) could stay in place as you scroll down (like Norvique and Chatterloop)
We will likely only use one image with a Company slogan on the Home page rather than a carousel of images to rotate through
Should not have
• This is the existing website: http://www.quelbrant-example.org
We do not like the animation, the way the banner icons/titles bounce
Not simple enough, we don't like the functionality or how pages load so slowly
We do not like the logo centered - it should be at the left
The banner and its tabs should not be towards the right, we would like them to be centered, to go all the way across and to be below the logo

```html
<!DOCTYPE html>
<html lang="en">
<head>
<meta charset="utf-8">
<title>Quelbrant International</title>
<link rel="stylesheet" href="https://fonts.googleapis.com/css2?family=Montserrat:wght@400;600;700&family=Open+Sans:wght@300;400;600&family=Questrial&display=swap">
<style>
:root{
  --red:#d9232a;
  --red-bright:#e3141b;
  --orange:#e2662a;
  --ink:#1d2a33;
  --text:#333;
  --muted:#777;
  --panel:#eeeeee;
  --line:#dcdcdc;
  --footer:#363636;
  --footer-bottom:#151515;
  --white:#fff;
}
*{margin:0;padding:0;box-sizing:border-box}
html,body{width:979px;height:1200px;overflow:hidden;background:var(--white)}
body{position:relative;font-family:"Open Sans",sans-serif;color:var(--text)}
.abs{position:absolute}

/* header */
.site-header{left:0;top:0;width:979px;height:110px;border-bottom:4px solid var(--red-bright);height:114px}
.brand{left:89px;top:34px;display:flex;align-items:center;gap:12px}
.brand-mark{width:30px;height:30px;background:var(--red)}
.brand-name{font-family:"Montserrat",sans-serif;font-weight:700;font-size:20px;letter-spacing:5px;color:var(--red)}
.search{left:635px;top:24px;width:230px;height:28px;border:1px solid #ccc;font-size:9px;color:#666;padding:8px 9px}
.search-icon{left:873px;top:31px}
.main-nav{left:0;top:77px;width:979px;font-family:"Montserrat",sans-serif;font-size:11.3px;color:#111}
.main-nav a{position:absolute;text-decoration:none;color:inherit;white-space:nowrap}
.main-nav a.active{color:var(--red-bright)}

/* hero */
.hero{left:0;top:114px;width:979px;height:364px;background:radial-gradient(circle at 72% 40%,#4a6b78 0%,#22404c 35%,#14303b 70%,#0f2630 100%)}
.hero-title{left:88px;top:226px;font-family:"Montserrat",sans-serif;font-weight:600;font-size:34px;line-height:45px;letter-spacing:2px;color:var(--white)}
.hero-title .hl{color:var(--red)}
.hero-btn{left:91px;top:375px;width:137px;height:31px;background:var(--red);border-radius:3px;color:var(--white);font-family:"Montserrat",sans-serif;font-weight:700;font-size:11px;letter-spacing:1.5px;display:flex;align-items:center;justify-content:center;gap:4px}
.dot{top:448px;width:8px;height:8px;border-radius:50%;background:var(--white)}
.dot.current{width:13px;height:13px;top:445px;background:var(--red)}

/* services */
.services-box{left:90px;top:508px;width:204px;height:198px;background:var(--panel)}
.services-title{left:90px;top:515px;width:204px;text-align:center;font-family:"Questrial",sans-serif;font-size:20px;letter-spacing:1px;color:var(--red)}
.services-rule{left:101px;top:546px;width:181px;height:2px;background:var(--red)}
.services-notch{left:187px;top:543px;width:6px;height:6px;background:var(--red);transform:rotate(45deg)}
.service-item{left:104px;display:flex;align-items:center;gap:14px;font-family:"Montserrat",sans-serif;font-size:13.5px;color:#222}
.service-item svg{width:33px;height:33px}

.tab{top:509px;height:40px;border:1px solid #ddd;border-bottom:none;background:#ececec;font-family:"Montserrat",sans-serif;font-size:13px;color:#222;display:flex;align-items:center;justify-content:center}
.tab.active{background:var(--white)}
.tab-rule{left:476px;top:548px;width:413px;height:1px;background:#ddd}
.tab-panel{left:305px;top:549px;width:584px;height:158px;background:linear-gradient(#fff,#f1f1f1)}
.tab-art{left:325px;top:579px;width:128px;height:88px;border-radius:44px 44px 8px 8px;background:linear-gradient(#9a9a9a,#7a7a7a)}
.tab-heading{left:470px;top:574px;font-family:"Questrial",sans-serif;font-size:21.5px;letter-spacing:1.5px;color:var(--red)}
.tab-text{left:472px;top:605px;width:410px;font-family:"Montserrat",sans-serif;font-size:10.8px;line-height:19px;color:#333}

/* news + works */
.section-title{top:742px;font-family:"Montserrat",sans-serif;font-weight:600;font-size:22px;letter-spacing:1.5px;color:var(--ink)}
.section-rule{top:786px;height:2px;background:#e5e5e5}
.news-title{left:92px;top:799px;font-family:"Questrial",sans-serif;font-size:18px;letter-spacing:.5px;color:var(--red)}
.news-date{left:92px;top:828px;font-size:9px;color:#444}
.news-text{left:92px;top:852px;width:430px;font-size:11.4px;font-weight:300;line-height:18px;color:#555}
.news-text .link{color:#3a7bbf}
.more{font-size:10.3px;font-weight:300;color:var(--orange)}
.works-list{left:560px;top:807px;width:316px;list-style:none}
.works-list li{position:relative;padding-left:20px;font-size:11.4px;font-weight:300;line-height:14px;color:#444;margin-bottom:7px}
.works-list li::before{content:"→";position:absolute;left:2px;top:0;font-size:10px;color:#555}
.works-rule{left:560px;top:902px;width:316px;height:1px;background:#e5e5e5}

/* footer */
.site-footer{left:0;top:973px;width:979px;height:186px;background:var(--footer)}
.footer-brand{left:80px;top:1003px;display:flex;align-items:center;gap:10px}
.footer-brand .brand-mark{background:var(--white);width:26px;height:26px}
.footer-brand .brand-name{color:var(--white);font-size:17px}
.footer-about{left:84px;top:1066px;width:275px;font-size:10.4px;line-height:16.3px;color:var(--white)}
.footer-col h3{font-size:12.8px;font-weight:600;color:var(--white);margin-bottom:9px}
.footer-col ul{list-style:none}
.footer-col li{font-size:10.4px;line-height:16.3px;color:var(--white)}
.mail-input{left:697px;top:1024px;width:143px;height:29px;background:var(--white);font-size:10px;color:#333;padding:8px 6px}
.mail-join{left:840px;top:1024px;width:52px;height:29px;background:var(--red-bright);color:var(--white);font-size:11.5px;font-weight:600;display:flex;align-items:center;justify-content:center}
.copyright{left:0;top:1159px;width:979px;height:41px;background:var(--footer-bottom);color:#ddd;font-size:10.5px;display:flex;align-items:center;justify-content:center}
</style>
</head>
<body>

<header class="abs site-header">
  <div class="abs brand"><span class="brand-mark"></span><span class="brand-name">QUELBRANT</span></div>
  <div class="abs search">Search Here ..........</div>
  <svg class="abs search-icon" width="14" height="14" viewBox="0 0 14 14"><circle cx="5.5" cy="5.5" r="4.3" fill="none" stroke="#999" stroke-width="1.8"/><line x1="8.6" y1="8.6" x2="12.5" y2="12.5" stroke="#999" stroke-width="2"/></svg>
  <nav class="abs main-nav">
    <a class="active" style="left:399px">HOME</a>
    <a style="left:456px">ABOUT US</a>
    <a style="left:537px">BUSINESS UNITS</a>
    <a style="left:651px">SERVICES</a>
    <a style="left:727px">LOCATIONS</a>
    <a style="left:816px">CONTACT US</a>
  </nav>
</header>

<section class="abs hero" role="img" aria-label="Consultant touching a glowing wireframe world map"></section>
<h1 class="abs hero-title">FINANCIAL AND<br><span class="hl">TECHNOLOGY</span> SPACE<br>FOR <span class="hl">TRANSPORTATION</span></h1>
<div class="abs hero-btn">LEARN MORE
  <svg width="22" height="10" viewBox="0 0 22 10"><path d="M1 1l5 4-5 4M8 1l5 4-5 4" fill="none" stroke="#fff" stroke-width="1.4"/></svg>
</div>
<span class="abs dot" style="left:482px"></span>
<span class="abs dot" style="left:499px"></span>
<span class="abs dot current" style="left:518px"></span>

<aside class="abs services-box"></aside>
<h2 class="abs services-title">Services</h2>
<div class="abs services-rule"></div>
<div class="abs services-notch"></div>
<div class="abs service-item" style="top:566px">
  <svg viewBox="0 0 34 34"><circle cx="17" cy="17" r="11" fill="none" stroke="#d9232a" stroke-width="5" stroke-dasharray="5 3.6"/><circle cx="17" cy="17" r="7" fill="none" stroke="#d9232a" stroke-width="2.5"/><line x1="12" y1="12" x2="22" y2="22" stroke="#d9232a" stroke-width="3"/></svg>
  Quelbrant Consulting</div>
<div class="abs service-item" style="top:614px">
  <svg viewBox="0 0 34 34" fill="none" stroke="#d9232a" stroke-width="1.6"><rect x="2" y="6" width="6" height="6"/><rect x="2" y="15" width="6" height="6"/><rect x="11" y="15" width="6" height="6"/><rect x="2" y="24" width="6" height="6"/><rect x="11" y="24" width="6" height="6"/><rect x="20" y="24" width="6" height="6"/><rect x="13" y="4" width="6" height="6" transform="rotate(20 16 7)"/><rect x="24" y="2" width="6" height="6" transform="rotate(30 27 5)"/><rect x="22" y="13" width="6" height="6" transform="rotate(15 25 16)"/></svg>
  Engineering</div>
<div class="abs service-item" style="top:657px">
  <svg viewBox="0 0 34 34"><circle cx="17" cy="17" r="11" fill="none" stroke="#d9232a" stroke-width="5" stroke-dasharray="5 3.6"/><circle cx="17" cy="17" r="7" fill="none" stroke="#d9232a" stroke-width="2.5"/><line x1="12" y1="12" x2="22" y2="22" stroke="#d9232a" stroke-width="3"/></svg>
  Quelbrant Consulting</div>

<div class="abs tab active" style="left:305px;width:171px">Quelbrant Consulting</div>
<div class="abs tab" style="left:481px;width:181px">System Energy</div>
<div class="abs tab" style="left:667px;width:169px">Amet Technology</div>
<div class="abs tab-rule"></div>
<div class="abs tab-panel"></div>
<div class="abs tab-art" role="img" aria-label="Cloud illustration with a group of business people"></div>
<h3 class="abs tab-heading">Sitquetamet dolor Ipsum amet</h3>
<p class="abs tab-text">quelbrant specializes in delivering quality professional services and technical projects that support larger business goals.&nbsp; systems are tools that support a greater business function and need. we understand that most t echnical projects are conceptualized to support a larger vision with actual</p>

<h2 class="abs section-title" style="left:94px">Latest News</h2>
<div class="abs section-rule" style="left:89px;width:427px"></div>
<h3 class="abs news-title">Coraz mniej serwerów, coraz więcej chmury</h3>
<div class="abs news-date">31 stycznia 2014</div>
<p class="abs news-text">Według <span class="link">Datarion</span>, szefowie <span class="link">IT</span> coraz szybciej przesiadają się do chmury obliczeniow między 25-30% wszystkich sprzedanych serwerów trafi nie do korporacyjnych..</p>
<div class="abs more" style="left:92px;top:903px">Czytaj więcej →</div>

<h2 class="abs section-title" style="left:570px">Featured Works</h2>
<div class="abs section-rule" style="left:560px;width:309px"></div>
<ul class="abs works-list">
  <li>Nasi eksperci publikują na Rackowisko: Corvane Flex System – integracja z Halvix vCore</li>
  <li>UE: 2,5 mln nowych miejsc pracy dzięki chmurze?</li>
  <li>E-seminarium: Zwiększania efektywności biznesu poprzez zastosowanie chmury obliczeniowej</li>
</ul>
<div class="abs works-rule"></div>
<div class="abs more" style="left:560px;top:925px">Wszystkie aktualności →</div>

<footer class="abs site-footer"></footer>
<div class="abs footer-brand"><span class="brand-mark"></span><span class="brand-name">QUELBRANT</span></div>
<p class="abs footer-about">Lorem ipsum dolorSit amet consecteturAdipsicing elit, ed do euismodTempor incidunt Labore et dolor Magna aliqua.Lorem ipsum dolorSit amet consec-teturAdipsicing elit,</p>
<div class="abs footer-col" style="left:388px;top:993px">
  <h3>Business Units</h3>
  <ul><li>Lorem ipsum</li><li>Is simply dummy</li><li>Text of the</li><li>Printing</li><li>And typesrtting</li><li>Industry</li></ul>
</div>
<div class="abs footer-col" style="left:564px;top:993px">
  <h3>Site Map</h3>
  <ul style="margin-left:5px"><li>Lorem ipsum</li><li>Is simply dummy</li><li>Text of the</li><li>Printing</li><li>And typesrtting</li><li>Industry</li></ul>
</div>
<div class="abs footer-col" style="left:700px;top:993px"><h3>Join Our Mailing List</h3></div>
<div class="abs mail-input">Enter your email address...</div>
<div class="abs mail-join">JOIN</div>
<div class="abs copyright">Copyrights © 2014Quelbrant.com - All Rights Reserved</div>

</body>
</html>
```